R. Talmont Realty, Inc business card (2 sided), letterhead (1 sided) & #10 envelope (1 sided)

business card of standard size utilizing the attached logo. Side one with logo, Owen Talmont (my name), President / Broker (title), 805-317-2684 (phone), www.rtalmontrealty.example (website), 1726 Harlow Avenue, Suite 4052 San Luis Obiso, CA 93628 (business address) owen.rtalmontrealty@mailbox.example (e-mail address),
Side two - Log

Letterhead and #10 envelope in the same theme
Updates

Project Deadline Extended
Reason: I think a 2 day deadline may be a bit ambitious on my part. I have extended the deadline to 4 days. Thanks!

Industry/Entity Type

Business

```html
<!DOCTYPE html>
<html lang="en">
<head>
<meta charset="utf-8">
<title>R. Talmont Realty, Inc – Business Card</title>
<link href="https://fonts.googleapis.com/css2?family=Questrial&display=swap" rel="stylesheet">
<style>
  :root {
    --brand-blue: #1f8fcf;
    --brand-blue-deep: #137ab8;
    --brand-blue-light: #3fa6de;
    --ink: #3d3d3d;
    --muted: #8a8a8a;
    --paper: #ffffff;
    --backdrop: #ecebe8;
  }
  * { margin: 0; padding: 0; box-sizing: border-box; }
  html, body {
    width: 1200px; height: 1184px; overflow: hidden;
    background: var(--backdrop);
    font-family: "Questrial", "Century Gothic", sans-serif;
  }
  .sheet { position: relative; width: 1200px; height: 1184px; }
  .card {
    position: absolute; left: 180px; width: 840px; height: 480px;
    overflow: hidden; box-shadow: 0 6px 22px rgba(0,0,0,0.18);
  }

  /* Front side */
  .card--front {
    top: 80px;
    background: linear-gradient(135deg, var(--brand-blue-light), var(--brand-blue-deep));
    color: var(--paper);
  }
  .front-brand {
    position: absolute; left: 0; right: 0; top: 168px;
    display: flex; align-items: center; justify-content: center; gap: 22px;
  }
  .front-brand__mark { width: 34px; height: 34px; background: var(--paper); }
  .front-brand__name { font-size: 62px; letter-spacing: 1px; }
  .front-web {
    position: absolute; left: 0; right: 0; top: 300px;
    text-align: center; font-size: 20px; letter-spacing: 4px;
  }

  /* Back side */
  .card--back {
    top: 624px;
    background: linear-gradient(160deg, #ffffff 55%, #eef0f2);
  }
  .back-brand {
    position: absolute; left: 56px; top: 92px;
    display: flex; align-items: center; gap: 12px;
  }
  .back-brand__mark { width: 16px; height: 16px; background: var(--brand-blue); }
  .back-brand__name { font-size: 30px; color: var(--ink); }

  .holder { position: absolute; left: 470px; top: 70px; }
  .holder__name { font-size: 36px; letter-spacing: -0.5px; text-transform: uppercase; }
  .holder__first { color: var(--brand-blue); }
  .holder__last { color: var(--ink); }
  .holder__title {
    margin-top: 4px; font-size: 17px; letter-spacing: 8px;
    color: var(--muted); text-transform: uppercase;
  }

  .contacts { position: absolute; left: 470px; top: 170px; list-style: none; }
  .contacts li {
    display: flex; align-items: center; gap: 12px;
    font-size: 19px; color: var(--ink); line-height: 34px;
  }
  .contacts svg { width: 18px; height: 18px; fill: var(--brand-blue); flex: none; }

  .wave { position: absolute; left: 0; bottom: 0; width: 840px; height: 240px; }
  .address {
    position: absolute; left: 56px; bottom: 44px;
    display: flex; align-items: flex-start; gap: 12px;
    color: var(--paper); font-size: 21px; line-height: 30px;
  }
  .address svg { width: 18px; height: 24px; fill: var(--paper); margin-top: 3px; }
</style>
</head>
<body>
<main class="sheet">

  <section class="card card--front" aria-label="Business card front">
    <div class="front-brand">
      <span class="front-brand__mark"></span>
      <span class="front-brand__name">R. Talmont Realty, Inc</span>
    </div>
    <p class="front-web">www.rtalmontrealty.example</p>
  </section>

  <section class="card card--back" aria-label="Business card back">
    <div class="back-brand">
      <span class="back-brand__mark"></span>
      <span class="back-brand__name">R. Talmont Realty, Inc</span>
    </div>

    <div class="holder">
      <p class="holder__name"><span class="holder__first">Owen</span><span class="holder__last">Talmont</span></p>
      <p class="holder__title">Broker</p>
    </div>

    <ul class="contacts">
      <li>
        <svg viewBox="0 0 18 18" aria-hidden="true"><path d="M5 1h8a1.5 1.5 0 0 1 1.5 1.5v13A1.5 1.5 0 0 1 13 17H5a1.5 1.5 0 0 1-1.5-1.5v-13A1.5 1.5 0 0 1 5 1zm0 2.5v10h8v-10z"/></svg>
        805-317-2684
      </li>
      <li>
        <svg viewBox="0 0 18 18" aria-hidden="true"><path d="M1 4h16v10H1zm1.5 1.2V6l6.5 4 6.5-4v-.8L9 9z"/></svg>
        owen.rtalmontrealty@mailbox.example
      </li>
      <li>
        <svg viewBox="0 0 18 18" aria-hidden="true"><path d="M9 1a8 8 0 1 0 0 16A8 8 0 0 0 9 1zm0 1.6c.9 0 1.9 1.7 2.3 4.4H6.7C7.1 4.3 8.1 2.6 9 2.6zM2.7 7.9h3.5a15 15 0 0 0 0 2.2H2.7a6.4 6.4 0 0 1 0-2.2zm9.1 0h3.5a6.4 6.4 0 0 1 0 2.2h-3.5a15 15 0 0 0 0-2.2zM6.7 11h4.6c-.4 2.7-1.4 4.4-2.3 4.4S7.1 13.7 6.7 11z"/></svg>
        www.rtalmontrealty.example
      </li>
    </ul>

    <svg class="wave" viewBox="0 0 840 240" preserveAspectRatio="none" aria-hidden="true">
      <path d="M0 118 C180 70 360 90 520 112 C660 130 760 90 840 30" fill="none" stroke="var(--brand-blue)" stroke-width="3"/>
      <path d="M0 136 C180 88 360 108 520 130 C660 148 760 110 840 50 L840 240 L0 240 Z" fill="var(--brand-blue)"/>
      <path d="M0 150 C180 104 360 124 520 144" fill="none" stroke="#ffffff" stroke-width="4" opacity="0.9"/>
    </svg>

    <div class="address">
      <svg viewBox="0 0 18 24" aria-hidden="true"><path d="M9 0a8 8 0 0 0-8 8c0 6 8 16 8 16s8-10 8-16a8 8 0 0 0-8-8zm0 11a3 3 0 1 1 0-6 3 3 0 0 1 0 6z"/></svg>
      <p>1726 Harlow Avenue,<br>Suite 4052 San Luis Obiso, CA 93628</p>
    </div>
  </section>

</main>
</body>
</html>
```